Construction material supplies company business card ****

1. Full company name “K T Masonry Works Ltd”
I am after a Business card design for the company as a whole. We are better known in Solomon Islands as “K T Masonry” for short.

We are a building materials supplier of
Ready Mixed Concrete, Bricks and Blocks,
Quarry products- gravel, aggregates, sand etc.
Cement distributor/retailer of reputable brands.
Other prefab concrete products. Culverts, wave breakers, concrete retaining blocks etc.

2. Competitive Advantage over Competition: Quality, efficient, professional, dependable, reliable

3. We want people to feel trust worthy, high quality, strong when they see our brand

5. No preference to color. Maybe more sturdy and corporate. Not fancy.

Industry/Entity Type

CONSTRUCTION SUPPLY

Contact Information for Business Card

Name, Position, office phone mob phone, email

Requirements
Must have
• the company logo
Nice to have
• would like to see a mixture of designs, of with logo only and also with simple graphic designs to bring out the company whilst still have the strong sturdy professional feeling

```html
<!DOCTYPE html>
<html lang="en">
<head>
<meta charset="utf-8">
<title>K T Masonry – Business Card</title>
<link href="https://fonts.googleapis.com/css2?family=Roboto:wght@400;500;700&display=swap" rel="stylesheet">
<style>
  :root {
    --navy: #1d4268;
    --band: #214b74;
    --card-light: #ececec;
    --card-mid: #dcdcdc;
    --page: #f2f2f2;
    --band-text: #e9edf2;
  }
  * { box-sizing: border-box; margin: 0; padding: 0; }
  html, body { width: 1200px; height: 1138px; overflow: hidden; }
  body {
    background: var(--page);
    font-family: "Roboto", Arial, sans-serif;
    color: var(--navy);
    position: relative;
  }
  .card {
    position: absolute;
    border-radius: 16px;
    overflow: hidden;
    background: radial-gradient(ellipse at 40% 30%, var(--card-light), var(--card-mid));
    box-shadow: 0 4px 12px rgba(0,0,0,.18);
  }
  .card--front { left: 274px; top: 186px; width: 623px; height: 376px; }
  .card--back  { left: 276px; top: 608px; width: 618px; height: 374px; }

  /* front */
  .wordmark {
    position: absolute; left: 0; right: 0; top: 70px;
    text-align: center;
    font-weight: 700; font-size: 50px; letter-spacing: 3px;
    text-transform: uppercase;
  }
  .intro-band {
    position: absolute; left: 0; right: 0; top: 214px; height: 79px;
    background: var(--band);
  }
  .intro-pill {
    position: absolute; left: 137px; top: 186px; width: 348px; height: 42px;
    border-radius: 21px;
    background: var(--band);
    border: 2px solid #f4f4f4;
    color: var(--band-text);
    font-size: 16px;
    display: flex; align-items: center; justify-content: center;
  }
  .supply-list {
    position: absolute; left: 0; right: 0; top: 239px;
    text-align: center; color: var(--band-text);
    font-size: 16px; line-height: 22px;
  }
  .other-list {
    position: absolute; left: 0; right: 0; top: 306px;
    text-align: center; font-size: 16px; line-height: 24px;
  }

  /* back */
  .brand-block {
    position: absolute; left: 80px; top: 120px; width: 190px;
    text-align: center;
  }
  .brand-square {
    width: 44px; height: 44px; background: var(--navy);
    margin: 0 auto 14px;
  }
  .brand-name { font-weight: 700; font-size: 30px; line-height: 34px; text-transform: uppercase; }
  .person { position: absolute; left: 312px; top: 62px; }
  .person__name { font-weight: 700; font-size: 23px; }
  .person__role { font-size: 17px; margin-top: 3px; }
  .contacts { position: absolute; left: 312px; top: 132px; font-size: 17px; line-height: 26px; }
  .contacts li { list-style: none; display: flex; align-items: center; }
  .contacts svg { width: 16px; height: 16px; margin-right: 16px; fill: var(--navy); }
  .rule { position: absolute; left: 0; right: 0; top: 322px; height: 5px; background: var(--band); }
  .values {
    position: absolute; left: 0; right: 0; top: 333px; height: 41px;
    background: var(--band); color: var(--band-text);
    display: flex; align-items: center; justify-content: center;
    font-size: 17px; word-spacing: 2px;
  }
</style>
</head>
<body>

<section class="card card--front">
  <h1 class="wordmark">K T Masonry</h1>
  <div class="intro-band"></div>
  <div class="intro-pill">We are a building materials supplier of</div>
  <p class="supply-list">Ready Mixed Concrete, Bricks and Blocks, Quarry Products<br>Quarry Products:- Gravel, Aggregates, Sand Etc.</p>
  <p class="other-list">Cement Distributor/Retailer of Reputable Brands.<br>Other Concrete Products Culverts, Wave Breakers, Concrete Retaining Blocks</p>
</section>

<section class="card card--back">
  <div class="brand-block">
    <div class="brand-square"></div>
    <div class="brand-name">K T<br>Masonry</div>
  </div>
  <div class="person">
    <div class="person__name">Daniel Mercer</div>
    <div class="person__role">Managing Director</div>
  </div>
  <ul class="contacts">
    <li><svg viewBox="0 0 16 16"><path d="M2 5c0-2 3-3 6-3s6 1 6 3v1h-3V5H5v1H2z"/><rect x="3" y="7" width="10" height="7" rx="1"/></svg>677 2041 5588</li>
    <li><svg viewBox="0 0 16 16"><path d="M1 3h14v10H1z M2 4l6 5 6-5" fill="none" stroke="#1d4268" stroke-width="1.6"/></svg>daniel@ktmasonry.com</li>
    <li><svg viewBox="0 0 16 16"><circle cx="8" cy="8" r="6.5" fill="none" stroke="#1d4268" stroke-width="1.4"/><path d="M1.5 8h13M8 1.5c-3 3.5-3 9.5 0 13M8 1.5c3 3.5 3 9.5 0 13" fill="none" stroke="#1d4268" stroke-width="1.2"/></svg>www.ktmasonry.com</li>
    <li>58 Harbour Rd., Port City,</li>
    <li>Coast Town, US 204817</li>
  </ul>
  <div class="rule"></div>
  <div class="values">Quality &nbsp;|&nbsp; Efficient &nbsp;|&nbsp; Professional &nbsp;|&nbsp; Dependable &nbsp;|&nbsp; Reliable</div>
</section>

</body>
</html>
```